ULMIRA card Technical Architecture

Hello everyone ULMIRA: It is a consulting firm in Architecture and Construction. I require a card duplexing, sober, elegant, classic but not boring. Update 1: Use the following data for the card. Name: Gonzalo Pereda Mauricio Villalta Position: COO Twitter: @ulmiraAT Homepage: ulmira-example.com home address not include the participation of all thank you.

Target Market(s)

Construction companies, Architects and Consulting Engineers

Industry/Entity Type

Consulting

Contact Information for Business Card

Los campos que debe tener:
Nombre, Cargo, email, homepage y twitter

Font styles to use
Serif
Sans Serif
Other font styles liked:
• Me gustan playfair display, open sans y roboto, pero estoy sujeto a sus propuestas

Requirements
Must have
• Colors: Present combined proposals in white, red, gray and black Update 1: The two names must be clearly differentiated from the two surnames
Nice to have
• They are free to present their best proposals. I will bring them immediate feedback to the extent you can go see their designs. Complete data for card and logo files will give the winner the

```html
<!DOCTYPE html>
<html lang="es">
<head>
<meta charset="utf-8">
<title>ULMIRA – Tarjeta de presentación</title>
<link rel="stylesheet" href="https://fonts.googleapis.com/css2?family=Montserrat:wght@400;500;700&display=swap">
<style>
  :root {
    --page-bg: #e6e4e4;
    --red-light: #b51f27;
    --red-dark: #5a080d;
    --wine: #7a1016;
    --ink: #2b2b2b;
    --white: #ffffff;
  }
  * { box-sizing: border-box; margin: 0; padding: 0; }
  html, body {
    width: 1200px; height: 900px; overflow: hidden;
    background: var(--page-bg);
    font-family: "Montserrat", sans-serif;
  }
  .sheet {
    width: 1200px; height: 900px;
    display: flex; flex-direction: column; align-items: center; justify-content: center;
    gap: 48px;
  }
  .card {
    position: relative;
    width: 620px; height: 354px;
    border-radius: 22px;
    overflow: hidden;
    box-shadow: 0 10px 28px rgba(0,0,0,.22);
  }

  /* Front */
  .card--front {
    background: radial-gradient(ellipse at 50% 35%, var(--red-light) 0%, #8c141b 45%, var(--red-dark) 100%);
    color: var(--white);
    display: flex; flex-direction: column; align-items: center; justify-content: center;
  }
  .brand-name {
    font-weight: 400;
    font-size: 58px;
    letter-spacing: 18px;
    margin-right: -18px;
    line-height: 1;
  }
  .brand-rule {
    width: 330px; height: 1px;
    background: rgba(255,255,255,.75);
    margin: 14px 0 8px;
  }
  .brand-tagline {
    font-size: 17px;
    font-weight: 400;
    letter-spacing: 5.5px;
    margin-right: -5.5px;
  }
  .social {
    margin-top: 26px;
    display: flex; align-items: center; gap: 8px;
    font-size: 14px;
  }
  .social-dot {
    width: 10px; height: 10px; border-radius: 50%;
    background: var(--white);
  }

  /* Back */
  .card--back { background: var(--white); }
  .edge-band {
    position: absolute; left: 0; bottom: 0;
    width: 34px; height: 178px;
    background: var(--wine);
    border-top-right-radius: 30px;
  }
  .brand-mark {
    position: absolute; top: 40px; right: 46px;
    font-weight: 700;
    font-size: 34px;
    letter-spacing: 4px;
    color: var(--wine);
  }
  .person {
    position: absolute; left: 66px; bottom: 40px;
  }
  .person-given, .person-family {
    font-weight: 700; font-size: 25px;
    color: var(--wine); line-height: 1.1;
  }
  .person-role {
    font-size: 14px; color: var(--ink);
    margin-bottom: 6px;
  }
  .contact-list { list-style: none; margin-top: 6px; }
  .contact-item {
    display: flex; align-items: center; gap: 8px;
    font-size: 15px; color: var(--ink); line-height: 1.5;
  }
  .contact-icon { width: 12px; height: 12px; flex: none; }
</style>
</head>
<body>
<main class="sheet">

  <section class="card card--front" aria-label="Anverso de la tarjeta">
    <div class="brand-name">ULMIRA</div>
    <div class="brand-rule"></div>
    <div class="brand-tagline">ARQUITECTURA TÉCNICA</div>
    <div class="social"><span class="social-dot"></span><span>@ulmiraAT</span></div>
  </section>

  <section class="card card--back" aria-label="Reverso de la tarjeta">
    <div class="brand-mark">ULMIRA</div>
    <div class="edge-band"></div>
    <div class="person">
      <div class="person-given">Gonzalo Pereda</div>
      <div class="person-role">COO</div>
      <div class="person-family">Mauricio Villalta</div>
      <div class="person-role">Director de Operaciones</div>
      <ul class="contact-list">
        <li class="contact-item">
          <svg class="contact-icon" viewBox="0 0 12 12"><path d="M2.5 1h2l1 2.5-1.3 1a6 6 0 0 0 3.3 3.3l1-1.3 2.5 1v2a1 1 0 0 1-1 1A9.5 9.5 0 0 1 1.5 2a1 1 0 0 1 1-1z" fill="#7a1016"/></svg>
          <span>(+57) 555 010 2030</span>
        </li>
        <li class="contact-item">
          <svg class="contact-icon" viewBox="0 0 12 12"><rect x="1" y="2.5" width="10" height="7" fill="none" stroke="#7a1016" stroke-width="1.3"/><path d="M1 2.5l5 4 5-4" fill="none" stroke="#7a1016" stroke-width="1.3"/></svg>
          <span>info@ulmira-example.com</span>
        </li>
        <li class="contact-item">
          <svg class="contact-icon" viewBox="0 0 12 12"><circle cx="6" cy="6" r="5" fill="none" stroke="#7a1016" stroke-width="1.2"/><ellipse cx="6" cy="6" rx="2.2" ry="5" fill="none" stroke="#7a1016" stroke-width="1"/><path d="M1 6h10" stroke="#7a1016" stroke-width="1"/></svg>
          <span>www.ulmira-example.com</span>
        </li>
      </ul>
    </div>
  </section>

</main>
</body>
</html>
```